Construction Company Facebook Banner

We are a small residential building company, building mostly new homes, renovations, extensions. our social media needs an uplift to look more professional.
I have no photos I wish to use in the banner as of yet however I have included the company logo, and the business card design which has some details.
I would like something simple but professional.
The banner does not need to have email, phone number, services provided etc. all of this is available on the facebook page itself. Something simple and clean please.
Industry/Entity Type
Construction
Requirements
Should not have
- Images of people, QR Code

```html
<!DOCTYPE html>
<html lang="en">
<head>
<meta charset="utf-8">
<title>Ridgeline Homes – Facebook Banner</title>
<link href="https://fonts.googleapis.com/css2?family=Orbitron:wght@700;800&family=Poppins:wght@400;500&family=Roboto+Condensed:wght@600&display=swap" rel="stylesheet">
<style>
  :root {
    --stage: #ebebeb;
    --white: #ffffff;
    --ink: #111111;
    --black: #040404;
    --green: #1fb841;
    --grey: #6a6a6a;
    --logo-grey: #3d3d3d;
    --divider: #1fb841;
  }
  * { margin: 0; padding: 0; box-sizing: border-box; }
  html, body { width: 1200px; height: 621px; overflow: hidden; background: var(--stage); }
  .banner {
    position: absolute; left: 70px; top: 77px; width: 1062px; height: 466px;
    overflow: hidden;
    background: linear-gradient(120deg, #ffffff 0%, #f3f3f3 30%, #ffffff 38%, #ededed 55%, #fafafa 70%);
    box-shadow: 0 6px 18px rgba(0,0,0,.22);
    font-family: "Poppins", sans-serif;
  }
  .shapes { position: absolute; inset: 0; }
  .brand { position: absolute; left: 40px; top: 38px; }
  .brand-mark { width: 40px; height: 40px; background: var(--green); margin-left: 75px; margin-bottom: 10px; }
  .brand-name {
    font-family: "Orbitron", sans-serif; font-weight: 700; color: var(--logo-grey);
    font-size: 19px; line-height: 1.1; letter-spacing: .3px;
  }
  .brand-name small { display: block; font-size: 8.5px; letter-spacing: .4px; }
  .headline {
    position: absolute; left: 40px; top: 140px;
    font-family: "Orbitron", sans-serif; font-weight: 800; font-size: 30px; line-height: 31px;
    letter-spacing: .5px; color: var(--ink);
  }
  .headline .accent { color: var(--green); display: block; }
  .services-panel {
    position: absolute; left: 0; top: 254px; width: 1062px; height: 212px;
    background: var(--black);
  }
  .services-title {
    position: absolute; left: 40px; top: 267px;
    font-family: "Orbitron", sans-serif; font-weight: 800; font-size: 20px; color: var(--white);
  }
  .services-title span { color: var(--green); }
  .services-list { position: absolute; left: 40px; top: 304px; list-style: none; }
  .service {
    position: absolute; display: flex; align-items: center; gap: 6px;
    color: var(--white); font-size: 15px; white-space: nowrap;
  }
  .service svg { width: 18px; height: 18px; flex: none; }
  .divider { position: absolute; top: 313px; width: 1.5px; height: 57px; background: var(--divider); }
  .photo {
    position: absolute; top: 234px; width: 148px; height: 148px;
    border: 2px solid var(--white);
  }
  .photo-roof { left: 689px; background: linear-gradient(160deg, #dbe6ef 0%, #b8c6d2 45%, #6b4b32 75%, #3c2a1c 100%); }
  .photo-saw { left: 867px; background: linear-gradient(135deg, #c9c3bb 0%, #8a7b6a 45%, #3d4f6a 75%, #b89a78 100%); }
  .contact {
    position: absolute; top: 398px; display: flex; align-items: center; gap: 8px;
    color: var(--white); font-size: 16px;
  }
  .contact svg { flex: none; }
  .contact-phone { left: 38px; font-family: "Roboto Condensed", sans-serif; font-weight: 600; font-size: 27px; }
  .contact-web { left: 306px; top: 402px; }
  .contact-mail { left: 600px; top: 402px; }
</style>
</head>
<body>
<div class="banner">
  <svg class="shapes" width="1062" height="466" viewBox="0 0 1062 466">
    <defs>
      <linearGradient id="houseTones" x1="0" y1="0" x2="0" y2="1">
        <stop offset="0" stop-color="#2f95e0"/>
        <stop offset=".35" stop-color="#cfd6db"/>
        <stop offset=".6" stop-color="#6d5443"/>
        <stop offset="1" stop-color="#7f8a6a"/>
      </linearGradient>
    </defs>
    <polygon points="934,0 1062,0 1062,347 730,135" fill="url(#houseTones)" role="img" aria-label="Photo of a newly built two-storey family home"/>
    <polygon points="626,83 766,0 934,0 730,135 626,199" fill="var(--green)"/>
    <polygon points="626,199 730,135 1062,347 1062,466 626,466" fill="var(--grey)"/>
  </svg>

  <div class="services-panel"></div>
  <svg class="shapes" width="1062" height="466" viewBox="0 0 1062 466">
    <polygon points="626,199 730,135 1062,347 1062,466" fill="var(--grey)"/>
  </svg>

  <div class="brand">
    <div class="brand-mark"></div>
    <div class="brand-name">RIDGELINE HOMES<small>AND BUILDS PTY LTD</small></div>
  </div>

  <h1 class="headline">LICENSED BUILDERS<span class="accent">CARPENTERS SERVICING</span><span class="accent">THE GOLDFIELDS, WA</span></h1>

  <h2 class="services-title"><span>OUR</span> SERVICES</h2>

  <ul class="services-list">
    <li class="service" style="left:0;top:0"><svg viewBox="0 0 20 20"><circle cx="10" cy="10" r="9" fill="var(--green)"/><path d="M5.5 10.3l3 3 6-6.2" stroke="#fff" stroke-width="2.2" fill="none"/></svg>New Homes</li>
    <li class="service" style="left:0;top:33px"><svg viewBox="0 0 20 20"><circle cx="10" cy="10" r="9" fill="var(--green)"/><path d="M5.5 10.3l3 3 6-6.2" stroke="#fff" stroke-width="2.2" fill="none"/></svg>Extensions</li>
    <li class="service" style="left:154px;top:0"><svg viewBox="0 0 20 20"><circle cx="10" cy="10" r="9" fill="var(--green)"/><path d="M5.5 10.3l3 3 6-6.2" stroke="#fff" stroke-width="2.2" fill="none"/></svg>Renovations</li>
    <li class="service" style="left:154px;top:33px"><svg viewBox="0 0 20 20"><circle cx="10" cy="10" r="9" fill="var(--green)"/><path d="M5.5 10.3l3 3 6-6.2" stroke="#fff" stroke-width="2.2" fill="none"/></svg>Bathrooms</li>
    <li class="service" style="left:317px;top:0"><svg viewBox="0 0 20 20"><circle cx="10" cy="10" r="9" fill="var(--green)"/><path d="M5.5 10.3l3 3 6-6.2" stroke="#fff" stroke-width="2.2" fill="none"/></svg>Carpentry</li>
    <li class="service" style="left:317px;top:33px"><svg viewBox="0 0 20 20"><circle cx="10" cy="10" r="9" fill="var(--green)"/><path d="M5.5 10.3l3 3 6-6.2" stroke="#fff" stroke-width="2.2" fill="none"/></svg>Sheds</li>
    <li class="service" style="left:454px;top:0"><svg viewBox="0 0 20 20"><circle cx="10" cy="10" r="9" fill="var(--green)"/><path d="M5.5 10.3l3 3 6-6.2" stroke="#fff" stroke-width="2.2" fill="none"/></svg>Carports</li>
    <li class="service" style="left:454px;top:33px"><svg viewBox="0 0 20 20"><circle cx="10" cy="10" r="9" fill="var(--green)"/><path d="M5.5 10.3l3 3 6-6.2" stroke="#fff" stroke-width="2.2" fill="none"/></svg>Patios</li>
  </ul>
  <span class="divider" style="left:174px"></span>
  <span class="divider" style="left:334px"></span>
  <span class="divider" style="left:480px"></span>

  <div class="photo photo-roof" role="img" aria-label="Photo of builders working on a timber roof frame"></div>
  <div class="photo photo-saw" role="img" aria-label="Photo of a carpenter cutting timber with a hand saw"></div>

  <div class="contact contact-phone">
    <svg width="32" height="30" viewBox="0 0 32 30" fill="none" stroke="var(--green)" stroke-width="2.4" stroke-linecap="round">
      <path d="M6 4l5 0 2 6-3 2.5c1.5 3.5 4 6 7.5 7.5L20 17l6 2v5c0 1-1 2-2 2C13 25 4 16 4 6c0-1 1-2 2-2z" fill="var(--green)" stroke="none"/>
      <path d="M19 3a9 9 0 0 1 8 8"/><path d="M18.5 8a4.5 4.5 0 0 1 4 4"/>
    </svg>
    +61 400 000 123
  </div>
  <div class="contact contact-web">
    <svg width="16" height="16" viewBox="0 0 16 16" fill="none" stroke="var(--green)" stroke-width="1.4">
      <circle cx="8" cy="8" r="6.5"/><ellipse cx="8" cy="8" rx="3" ry="6.5"/><path d="M1.5 8h13M2.6 4.5h10.8M2.6 11.5h10.8"/>
    </svg>
    www.ridgeline-homes.com
  </div>
  <div class="contact contact-mail">
    <svg width="16" height="13" viewBox="0 0 16 13" fill="none" stroke="var(--green)" stroke-width="1.4">
      <rect x="1" y="1" width="14" height="11"/><path d="M1 1.5l7 5.5 7-5.5"/>
    </svg>
    admin@ridgeline-homes.com
  </div>
</div>
</body>
</html>
```